Business Card Design Project - del varosi group

dear Sirs

we need business card design for our group ( DEL Varosi Group ) , i have got the Logo design of our group from pixel harbor in previous , so all need details relating to our group i think available with you, as well as the the chosen logo design

we hope to provide us with business card logo that to be appropaite and satisfactory to us .

thanks

note : logo design of our group is attached .
Updates

Reason: please extend the deadline of my project for additional 15 days because i didn't received appropriate design for our gruop yet . kindly beaware that i have received 77 design till now , supossed to send me 200-250 design at least . thanks

Target Market(s)

contents

name : Kerem EL Nadiri

position : Operation Manager

Industry/Entity Type

Business

Requirements
Must have

• person name

group logo
Nice to have
• logo color matching with back background

```html
<!DOCTYPE html>
<html lang="en">
<head>
<meta charset="utf-8">
<title>DEL Varosi Group – Business Card</title>
<link href="https://fonts.googleapis.com/css2?family=Ubuntu:wght@400;500&family=Exo+2:wght@400&display=swap" rel="stylesheet">
<style>
  :root {
    --page-bg: #e6e7e9;
    --card-black: #121315;
    --card-mid: #1d1f22;
    --panel-fill: #262527;
    --logo-grey: #a9abae;
    --logo-faint: #3b404b;
    --name-blue: #1f6fc0;
    --link-blue: #2f7fd0;
    --text-white: #f2f2f2;
  }
  * { margin: 0; padding: 0; box-sizing: border-box; }
  html, body { width: 1067px; height: 1200px; overflow: hidden; }
  body {
    background: var(--page-bg);
    font-family: "Ubuntu", sans-serif;
    position: relative;
  }
  .card {
    position: absolute;
    left: 103px;
    width: 860px;
    height: 490px;
    overflow: hidden;
    background: radial-gradient(ellipse at 50% 45%, var(--card-mid), var(--card-black) 75%);
    box-shadow: 0 10px 28px rgba(0,0,0,0.25);
  }
  .card--front { top: 75px; }
  .card--back { top: 635px; }
  .card__shapes { position: absolute; inset: 0; }
  .logo-name {
    position: absolute;
    left: 0; right: 0;
    text-align: center;
    font-family: "Ubuntu", sans-serif;
    font-weight: 400;
    text-transform: uppercase;
    letter-spacing: 2px;
    white-space: nowrap;
  }
  .card--front .logo-name {
    top: 62px;
    font-size: 44px;
    color: var(--logo-grey);
  }
  .card--back .logo-name {
    top: 205px;
    font-size: 62px;
    color: var(--logo-faint);
  }
  .holder {
    position: absolute;
    left: 0; right: 0;
    top: 206px;
    text-align: center;
  }
  .holder__name {
    font-family: "Exo 2", sans-serif;
    font-size: 38px;
    color: var(--name-blue);
    line-height: 1.1;
  }
  .holder__role {
    margin-top: 8px;
    font-size: 21px;
    color: var(--text-white);
  }
  .contact {
    position: absolute;
    left: 0; right: 0;
    top: 346px;
    text-align: center;
    list-style: none;
    font-size: 20px;
    line-height: 24px;
    color: var(--text-white);
  }
  .contact__link { color: var(--link-blue); }
</style>
</head>
<body>

  <section class="card card--front">
    <svg class="card__shapes" width="860" height="490" viewBox="0 0 860 490" aria-hidden="true">
      <defs>
        <linearGradient id="bevel" x1="0" x2="1" y1="0" y2="0">
          <stop offset="0" stop-color="#9fb3d6"/>
          <stop offset="0.2" stop-color="#3a5a9a"/>
          <stop offset="0.5" stop-color="#cfd6e4"/>
          <stop offset="0.8" stop-color="#3a5a9a"/>
          <stop offset="1" stop-color="#9fb3d6"/>
        </linearGradient>
      </defs>
      <path class="panel panel--top" d="M112 -4 Q150 187 212 187 L622 187 Q696 187 726 -4 Z"
            fill="var(--panel-fill)" stroke="url(#bevel)" stroke-width="7"/>
      <path class="panel panel--bottom" d="M128 494 Q160 316 226 316 L622 316 Q692 316 740 494 Z"
            fill="var(--panel-fill)" stroke="url(#bevel)" stroke-width="7"/>
    </svg>

    <div class="logo-name">DEL VAROSI GROUP</div>

    <div class="holder">
      <p class="holder__name">Kerem EL Nadiri</p>
      <p class="holder__role">Operation Manager</p>
    </div>

    <ul class="contact">
      <li>Phone: 0123 456 789</li>
      <li>Fax: 0123 456 789</li>
      <li class="contact__link">info yourdomain.com</li>
      <li class="contact__link">www.yourdomain.com</li>
      <li>P.O. Box: City name, etc.</li>
    </ul>
  </section>

  <section class="card card--back">
    <div class="logo-name">DEL VAROSI GROUP</div>
  </section>

</body>
</html>
```